I need a business card design for a new dance business. I offer classical Indian dance tuition and also professional performances. I want to offer the community a variety of Indian dance experiences which include: group class and private tuition, school and preschool educational courses and workshops. dance theatre performances, community function workshops and performances, Kids Bollywood parties, wedding & conference performances, mouth percussion classes, Indian mythology/ dance costume and make up workshops.
The final design should communicate a feeling and impression of the vibrance and energy of Indian dance.
Updates
Hi Everyone,
Project Deadline Extended
Reason: I would like to refine a few changes to the details of this lovely design and we have run out of time!
Project Deadline Extended
Reason: Still waiting to hear back form designer re two possible changes to the card design. Tomorrow is the deadline and I have sent several messages but with no response. I need to see this through before selecting this lovely design.
Thank you.
Tara
Industry/Entity Type
Preschool
Requirements
Must have
- The front of the business card should have the photo of me (my face and torso), surrounded entirely by a border of bright magenta (to match the magenta of my lipstick - it is the same as the magenta on my skirt in the second photo). Within the top border I want (perhaps yellow-gold) writing to say "Tara Holloway - Artistic Director" and within the bottom border it should read "Saffron Lantern Indian Dance." If you turn the card on its side the left border should have my telephone number: 0417 862 493 and the right-hand border should read: saffronlanternindiandance@quillmail.example
The reverse of the card should be the orange of the dance costume
and I'd like the picture of my feet and legs to be on the right side of the back of the card as a side border. Centre-aligned on the orange background it should read (perhaps in dark magenta):
Indian dance classes + private tuition
School + preschool educational courses and workshops
Dance theatre performances
Community function workshops and performances
Children's Bollywood parties
Wedding + conference performances
Mouth percussion classes
Indian mythology and dance demonstration workshops
Dance costume and make-up workshops
Nice to have
- A lovely artistic but easy-to-read font would be nice.

```html
<!DOCTYPE html>
<html lang="en">
<head>
<meta charset="utf-8">
<title>Saffron Lantern Indian Dance – Business Card</title>
<link href="https://fonts.googleapis.com/css2?family=Kurale&display=swap" rel="stylesheet">
<style>
  :root {
    --saffron: #e07a2e;
    --saffron-clear: rgba(224,122,46,0);
    --magenta: #d42a94;
    --plum: #6e1846;
    --gold: #d9a24a;
    --white: #ffffff;
    --page: #ffffff;
  }
  * { margin: 0; padding: 0; box-sizing: border-box; }
  html, body {
    width: 1200px; height: 900px; overflow: hidden;
    background: var(--page);
    font-family: "Kurale", Georgia, serif;
    font-variant-numeric: lining-nums;
  }
  .canvas { position: relative; width: 1200px; height: 900px; }
  .card { position: absolute; overflow: hidden; }

  /* Front */
  .card--front {
    left: 136px; top: 96px; width: 428px; height: 704px;
    background: var(--saffron);
  }
  .front__photo {
    position: absolute; left: 236px; top: 0; width: 192px; height: 629px;
    background:
      radial-gradient(ellipse 45% 22% at 55% 12%, rgba(110,24,70,0.9), transparent 70%),
      radial-gradient(ellipse 50% 30% at 65% 75%, rgba(217,162,74,0.9), transparent 70%),
      linear-gradient(90deg, var(--saffron-clear) 0%, rgba(180,34,120,0.85) 22%, rgba(190,40,120,0.9) 55%, rgba(217,162,74,0.8) 85%, rgba(224,122,46,0.7) 100%);
  }
  .front__title {
    position: absolute; left: 0; top: 392px; width: 232px;
    text-align: center; color: var(--magenta);
    font-size: 38px; line-height: 47px; font-weight: 400;
  }
  .front__name {
    position: absolute; left: 0; top: 586px; width: 244px;
    text-align: center; color: var(--white); font-size: 27px;
  }
  .front__phone-band {
    position: absolute; left: 0; bottom: 0; width: 100%; height: 75px;
    background: var(--magenta);
    display: flex; align-items: center; justify-content: center;
  }
  .front__phone { color: var(--saffron); font-size: 50px; letter-spacing: 1px; }

  /* Back */
  .card--back {
    left: 626px; top: 96px; width: 431px; height: 705px;
    background: var(--magenta);
  }
  .back__email-band {
    position: absolute; left: 0; top: 0; width: 100%; height: 79px;
    background: var(--saffron);
    display: flex; align-items: center; justify-content: center;
  }
  .back__email { color: var(--magenta); font-size: 17.5px; }
  .services {
    position: absolute; left: 0; top: 100px; width: 100%;
    list-style: none; text-align: center;
    color: var(--white); font-size: 15.5px; line-height: 17px;
  }
  .services li { margin-bottom: 16px; padding: 0 30px; }
  .back__photo {
    position: absolute; left: 44px; top: 462px; width: 365px; height: 243px;
    background:
      radial-gradient(ellipse 30% 40% at 50% 70%, rgba(217,162,74,0.95), transparent 70%),
      linear-gradient(180deg, rgba(212,42,148,0) 0%, rgba(200,60,120,0.6) 40%, rgba(225,160,60,0.8) 100%);
  }
</style>
</head>
<body>
<main class="canvas">
  <section class="card card--front">
    <div class="front__photo" role="img" aria-label="Photo of a dancer's legs and feet in a magenta and gold silk costume with ankle bells"></div>
    <h1 class="front__title">Saffron<br>Lantern<br>Indian<br>Dance</h1>
    <p class="front__name">Tara Holloway</p>
    <div class="front__phone-band">
      <p class="front__phone">0417 862 493</p>
    </div>
  </section>

  <section class="card card--back">
    <div class="back__email-band">
      <p class="back__email">saffronlanternindiandance@quillmail.example</p>
    </div>
    <ul class="services">
      <li>Indian dance classes + private tuition</li>
      <li>School + preschool educational courses<br>and workshops</li>
      <li>Dance theatre performances</li>
      <li>Community function workshops<br>and performances</li>
      <li>Children's Bollywood parties</li>
      <li>Wedding + conference performances</li>
      <li>Mouth percussion classes</li>
      <li>Indian mythology and dance demonstration<br>workshop</li>
      <li>Dance costume and make-up workshops</li>
    </ul>
    <div class="back__photo" role="img" aria-label="Photo of a classical Indian dancer in a gold and maroon costume holding a hand gesture"></div>
  </section>
</main>
</body>
</html>
```